Remote Game Console (Tavlin) Wpf/Web UI

A complete interface for a second generation remote console tool to administer PC games. Will primarily run as a desktop application with future plans of running within a browser.

All materials are supplied as a guide only, but the designer is free to build what they would find easy to use. We're engineers so help us out with a good user experience.

The first version of Tavlin Emberhold was released in March 2009 supporting Skyrend: Iron Platoon 2. It was updated later in the year to support the expansion, SRIP2: Kestrel. Crest of Valour followed in late 2010 and Skyrend 3 support in October 2011. All games are based on MORV's Emberhold engine. http://dravek.example/tavlin-emberhold/

Tavlin 2 will eventually support all games, working more along the lines of a framework for others to expand upon. While ultimately having a similar function as Tavlin Emberhold, Tavlin 2 has been completely rewritten and shares no similarities internally.

The primary focus of the application is to display details about a users rented Game Server. A user can kick, ban and chat with players in their servers. A user can alter the settings of their game server, setting the time of a round or the game servers name for instance.

We have a forum dedicated to this competition that users of our software can give general feedback about the existing (Tavlin Emberhold) software, such as what they hate etc. http://www.dravek.example/forumvb/forumdisplay.php?35-UI-Competition

You can find similar software with much cooler looking UI's at http://www.ip2xz.example/ and http://sk3xz.example/

The techy details:

Tavlin 2 can run locally or connect and login to a hosted version of the software (internally we call this a Local Interface or Remote Interface). Logging into a remote server requires an IP, port, username and password. Beyond the initial local/remote selection the UI can function identically.

1 Instance of the software has a single Local (no login required) or Remote (ip/port/username/password required) Interface.

1 Instance has many Packages. A package is an extension to the software that the user can install. A package can be an update to Tavlin 2 itself, a plugin or a config.

1 Instance has many Options. We are partial to Nuvex Lumas Options panel. Something similar which would allow us to expand would be neat.

1 Instance has many languages.

1 Interface has many Game Connections. A game connection requires an ip, port and password to connect and authenticate. A game connection has a name, maximum players allowed to connect, a game type (e.g iron platoon 2, crest of valour, skyrend 3).

1 Game Connection has many plugins. A plugin extends the functionality of the software in the background.

1 Game Connection has many players. A player has a name, country, score, ping, kills, deaths and other variables depending on the type of Game connected to.

1 Game Connection has many bans. A ban is a record of a player, the players identifying information, a small description of why the ban was put in place as well as an expiry time (e.g. banned for 2 weeks or permanently banned)

1 Game Connection has many settings. These settings can vary dramatically depending on the Game connected to.

1 Interface has many Groups. A group has a name any many permissions.

1 Group has many Accounts.

1 Account has many players.
Updates

Reason: Uploaded wireframes. I work a lot and this is my side project. I thought I would have wireframes the next day of this project, but it didn't end up like that. All current submissions have been the first iteration of my software reskinned, not the next version.

Target Market(s)

First Person Shooter PC game administrators

Industry/Entity Type

Software

Requirements
Must have
• Tavlin 2 has a primitive natural language parser for converting free text into commands for the program. An online functional example is available at http://labs.venta.example/the-thrifty-helper/ (check down the bottom). The design should incorporate a text box throughout the application for users to enter commands in. As the user types this could be passed to display what will happen once the user executes the command

Generally people will be minimizing their games to kick or ban people from their servers. The UI design should be easy enough to navigate quickly.

A UI that can handle multiple languages. Our primary market is Germany.

The UI must be usable at 1024x768. It should be designed to take up the maximum window/browser space.
Nice to have
• Responsive design that scales to any resolution. We have a large mobile user base that could benefit from a UI that scales well on lower resolutions.

Tavlin 2 has no set logo as of yet, though we will continue using the smiley found at http://dravek.example - we only have a 100 by 100px png of this image though. If a larger version is supplied you'll receive a virtual cookie and a thank you! The logo will probably end up as a variation of that found on http://dravek.example/tavlin-emberhold/ but we'll go through the exact process for this at a later date

```html
<!DOCTYPE html>
<html lang="en">
<head>
<meta charset="utf-8">
<title>Tavlin Emberhold – Chat</title>
<link href="https://fonts.googleapis.com/css2?family=PT+Sans:wght@400;700&display=swap" rel="stylesheet">
<style>
:root{
  --bg:#0b0b0b;
  --text:#d8d8d8;
  --muted:#b5b5b5;
  --accent:#ff9a1f;
  --blue:#3fa9f5;
  --btn-top:#ff7a3a;
  --btn-bot:#e4470c;
  --tab-top:#e6e6e6;
  --tab-bot:#9c9c9c;
  --field:#1c1c1c;
  --select-top:#8e8e8e;
  --select-bot:#555;
}
*{box-sizing:border-box;margin:0;padding:0}
html,body{width:1198px;height:1200px;overflow:hidden;background:var(--bg)}
body{font-family:"PT Sans",sans-serif;color:var(--text)}
.app{position:absolute;left:0;top:0;width:1024px;height:1026px;transform:scale(1.1699);transform-origin:0 0;background:var(--bg)}
.abs{position:absolute;white-space:nowrap}
.titlebar{left:0;top:0;width:1024px;height:46px;background:linear-gradient(#2a2a2a,#0e0e0e)}
.app-dot{left:20px;top:21px;width:11px;height:11px;border-radius:50%;background:#5a8fa8}
.app-title{left:44px;top:16px;font-size:17px;color:#eee}
.win-btn{top:12px;width:15px;height:15px;background:#ccc;border-radius:2px;color:#111;font-size:13px;font-weight:700;line-height:15px;text-align:center}
.menu{top:54px;font-size:12px;color:#ddd}
.nav-icon{top:80px}
.server-select{left:111px;top:80px;width:403px;height:22px;background:#fff;border:1px solid #999;font-size:11.5px;color:#111;display:flex;align-items:center;padding-left:6px;gap:6px}
.game-name{font-weight:700;font-size:10px;color:#222}
.tick{width:10px;height:10px;background:#7ac143;border:1px solid #4b8a1f}
.drop{position:absolute;right:2px;top:2px;width:16px;height:16px;background:#555}
.drop::after{content:"";position:absolute;left:4px;top:6px;border:4px solid transparent;border-top:5px solid #fff}
.auto-connect{left:527px;top:79px;width:161px;height:22px;background:#fff;font-size:11.5px;color:#111;display:flex;align-items:center;gap:6px;padding-left:6px}
.info{top:116px;font-size:12px;color:#ddd}
.info.link{color:var(--blue)}
.tabs{left:10px;top:141px;width:1004px;height:28px;background:linear-gradient(var(--tab-top),var(--tab-bot));border:1px solid #777;border-radius:2px}
.tab{top:7px;font-size:12px;color:#222}
.tab-active{left:74px;top:1px;width:60px;height:25px;background:linear-gradient(#555,#222);border:1px solid #999;border-radius:3px;color:#fff;font-size:12px;text-align:center;line-height:24px}
.chat-panel{left:10px;top:170px;width:1004px;height:692px;border:1px solid #333;background:radial-gradient(ellipse at 55% 60%,#3a3122 0%,#221d15 45%,#0f0d0a 100%)}
.chat-log{left:25px;top:192px;list-style:none;font-size:11.5px;color:var(--muted)}
.chat-log li{height:24px;line-height:16px}
.weapon{color:var(--accent)}
.scrollbar{left:998px;top:178px;width:10px;height:680px;background:#1a1a1a;border-radius:4px}
.thumb{left:999px;top:192px;width:8px;height:651px;background:#8a8a8a;border-radius:4px}
.control-panel{left:10px;top:872px;width:1004px;height:125px;border:1px solid #333;background:#111}
.chat-input{left:32px;top:883px;width:452px;height:25px;background:var(--field);border:1px solid #333}
.select{top:885px;height:22px;background:linear-gradient(var(--select-top),var(--select-bot));font-size:11.5px;color:#eee;padding:4px 8px}
.select .drop{background:#444;top:3px}
.btn{left:866px;width:120px;height:30px;border-radius:5px;background:linear-gradient(var(--btn-top),var(--btn-bot));border:1px solid #b33;color:#fff;font-size:12px;text-align:center;line-height:28px}
.check{left:34px;width:14px;height:14px;background:#ddd;border-radius:2px}
.check svg{display:block}
.check-label{left:65px;font-size:12px;color:#ccc}
.corner-label{left:986px;top:1006px;font-size:11px;color:#ddd}
</style>
</head>
<body>
<div class="app">
  <div class="abs titlebar"></div>
  <div class="abs app-dot"></div>
  <div class="abs app-title">Tavlin Emberhold</div>
  <div class="abs win-btn" style="left:948px">–</div>
  <div class="abs win-btn" style="left:967px">+</div>
  <div class="abs win-btn" style="left:986px">×</div>

  <div class="abs menu" style="left:12px">File</div>
  <div class="abs menu" style="left:39px">Tools</div>
  <div class="abs menu" style="left:75px">Help</div>

  <svg class="abs nav-icon" style="left:15px" width="26" height="22" viewBox="0 0 26 22"><path d="M2 11 13 2l11 9h-3v10h-6v-6h-4v6H5V11z" fill="#bbb"/></svg>
  <svg class="abs nav-icon" style="left:52px;top:84px" width="18" height="14" viewBox="0 0 18 14"><path d="M0 7 8 0v4h10v6H8v4z" fill="#999"/></svg>
  <svg class="abs nav-icon" style="left:83px;top:84px" width="18" height="14" viewBox="0 0 18 14"><path d="M18 7 10 0v4H0v6h10v4z" fill="#999"/></svg>

  <div class="abs server-select"><span class="game-name">SKYREND</span><span class="tick"></span>[32/32] Tavlin[kvrel.example - Deine Community !<span class="drop"></span></div>
  <div class="abs auto-connect"><span class="tick"></span>Automatically Connect</div>

  <div class="abs info" style="left:19px">Rush - Corvallo</div>
  <div class="abs info" style="left:127px">Round: 1/2</div>
  <svg class="abs" style="left:194px;top:116px" width="34" height="16" viewBox="0 0 34 16"><circle cx="7" cy="8" r="5" fill="none" stroke="#777" stroke-width="2"/><path d="M20 2h6v6h4l-7 7-7-7h4z" fill="#777"/></svg>
  <div class="abs info link" style="left:235px">Accepting Players</div>
  <div class="abs info" style="left:379px">Version: 584652 (R23)</div>
  <div class="abs info link" style="left:504px">0.6.2.0</div>

  <div class="abs tabs">
    <div class="abs tab" style="left:20px">Players</div>
    <div class="tab-active abs">Chat</div>
    <div class="abs tab" style="left:163px">Map</div>
    <div class="abs tab" style="left:236px">Events</div>
    <div class="abs tab" style="left:307px">Lists</div>
    <div class="abs tab" style="left:380px">Server Settings</div>
    <div class="abs tab" style="left:488px">Plugins</div>
    <div class="abs tab" style="left:559px">Accounts</div>
    <div class="abs tab" style="left:632px">Console</div>
    <div class="abs tab" style="left:704px">Parent Layer Control</div>
  </div>

  <div class="abs chat-panel" role="img" aria-label="Dark painted backdrop of an old sailing ship"></div>
  <ul class="abs chat-log">
    <li>[12:17:13] Korvane [<span class="weapon">Mortal Strike</span>] Umbra_Vex</li>
    <li>[12:17:13] Korvane [<span class="weapon">VKR Marksman Short</span>] Umbra_Vex [Headshot]</li>
    <li>[12:17:13] Korvane [<span class="weapon">R88 Longshot</span>] Umbra_Vex [Headshot]</li>
    <li>[12:17:13] Korvane [<span class="weapon">TK-40 Harrier</span>] Umbra_Vex [Headshot]</li>
    <li>[12:17:13] Korvane [<span class="weapon">Mortal Strike</span>] Umbra_Vex</li>
    <li>[12:17:13] Korvane [<span class="weapon">VKR Marksman Short</span>] Umbra_Vex [Headshot]</li>
    <li>[12:17:13] Korvane [<span class="weapon">R88 Longshot</span>] Umbra_Vex [Headshot]</li>
    <li>[12:17:13] Korvane [<span class="weapon">TK-40 Harrier</span>] Umbra_Vex [Headshot]</li>
    <li>[12:17:13] Korvane [<span class="weapon">Mortal Strike</span>] Umbra_Vex</li>
    <li>[12:17:13] Korvane [<span class="weapon">VKR Marksman Short</span>] Umbra_Vex [Headshot]</li>
    <li>[12:17:13] Korvane [<span class="weapon">R88 Longshot</span>] Umbra_Vex [Headshot]</li>
    <li>[12:17:13] Korvane [<span class="weapon">TK-40 Harrier</span>] Umbra_Vex [Headshot]</li>
    <li>[12:17:13] Korvane [<span class="weapon">Mortal Strike</span>] Umbra_Vex</li>
    <li>[12:17:13] Korvane [<span class="weapon">VKR Marksman Short</span>] Umbra_Vex [Headshot]</li>
    <li>[12:17:13] Korvane [<span class="weapon">R88 Longshot</span>] Umbra_Vex [Headshot]</li>
    <li>[12:17:13] Korvane [<span class="weapon">TK-40 Harrier</span>] Umbra_Vex [Headshot]</li>
    <li>[12:17:13] Korvane [<span class="weapon">Mortal Strike</span>] Umbra_Vex</li>
    <li>[12:17:13] Korvane [<span class="weapon">VKR Marksman Short</span>] Umbra_Vex [Headshot]</li>
    <li>[12:17:13] Korvane [<span class="weapon">R88 Longshot</span>] Umbra_Vex [Headshot]</li>
    <li>[12:17:13] Korvane [<span class="weapon">TK-40 Harrier</span>] Umbra_Vex [Headshot]</li>
    <li>[12:17:13] Korvane [<span class="weapon">Mortal Strike</span>] Umbra_Vex</li>
    <li>[12:17:13] Korvane [<span class="weapon">VKR Marksman Short</span>] Umbra_Vex [Headshot]</li>
    <li>[12:17:13] Korvane [<span class="weapon">R88 Longshot</span>] Umbra_Vex [Headshot]</li>
    <li>[12:17:13] Korvane [<span class="weapon">TK-40 Harrier</span>] Umbra_Vex [Headshot]</li>
    <li>[12:17:13] Korvane [<span class="weapon">Mortal Strike</span>] Umbra_Vex</li>
    <li>[12:17:13] Korvane [<span class="weapon">VKR Marksman Short</span>] Umbra_Vex [Headshot]</li>
  </ul>
  <div class="abs scrollbar"></div>
  <div class="abs thumb"></div>

  <div class="abs control-panel"></div>
  <div class="abs chat-input"></div>
  <div class="abs select" style="left:500px;width:126px">All Players<span class="drop"></span></div>
  <div class="abs select" style="left:641px;width:96px">Say<span class="drop"></span></div>
  <div class="abs select" style="left:751px;width:96px">2 Seconds<span class="drop"></span></div>
  <div class="abs btn" style="top:881px">Send</div>
  <div class="abs btn" style="top:922px">Clear Chat</div>

  <div class="abs check" style="top:920px"><svg width="14" height="14" viewBox="0 0 14 14"><path d="M3 7l3 3 5-6" fill="none" stroke="#111" stroke-width="2"/></svg></div>
  <div class="abs check-label" style="top:919px">Enable Scrolling</div>
  <div class="abs check" style="top:944px"><svg width="14" height="14" viewBox="0 0 14 14"><path d="M3 7l3 3 5-6" fill="none" stroke="#111" stroke-width="2"/></svg></div>
  <div class="abs check-label" style="top:943px">Display join/leaving</div>
  <div class="abs check" style="top:968px"><svg width="14" height="14" viewBox="0 0 14 14"><path d="M3 7l3 3 5-6" fill="none" stroke="#111" stroke-width="2"/></svg></div>
  <div class="abs check-label" style="top:967px">Display kills/deaths</div>

  <div class="abs corner-label">X6</div>
</div>
</body>
</html>
```